Flyers

Modify Existing Flyer and create another for exterior company
Updates

Previous Brief has been updated- we want to update this existing one also

Target Market(s)

Exterior Remodeling Customers

Industry/Entity Type

Remodeling/Construction

```html
<!DOCTYPE html>
<html lang="en">
<head>
<meta charset="utf-8">
<title>Northline Roofing and Exteriors – Remodeling Flyer</title>
<link href="https://fonts.googleapis.com/css2?family=Poppins:wght@400;500;600;700;800&display=swap" rel="stylesheet">
<style>
  :root{
    --blue:#1e72bb;
    --orange:#f15a29;
    --black:#0b0b0b;
    --ink:#141414;
    --white:#ffffff;
    --page:#ffffff;
  }
  *{margin:0;padding:0;box-sizing:border-box}
  html,body{width:849px;height:1200px;overflow:hidden;background:var(--page)}
  body{font-family:'Poppins',sans-serif;color:var(--ink)}
  .flyer{position:relative;width:849px;height:1200px;overflow:hidden;background:var(--page)}
  .shapes{position:absolute;inset:0}

  .brand{position:absolute;left:0;top:16px;width:290px;text-align:center;color:var(--white);font-weight:600;line-height:1}
  .brand-name{display:block;font-size:42px;letter-spacing:2px}
  .brand-tag{display:block;font-size:14.5px;letter-spacing:.6px;margin-top:14px;border-top:1.5px solid var(--white);border-bottom:1.5px solid var(--white);padding:4px 0;width:230px;margin-left:auto;margin-right:auto}

  .hero{position:absolute;left:25px;top:170px;color:var(--white);white-space:nowrap}
  .hero-lead{font-size:31px;font-weight:400;line-height:37.7px;letter-spacing:-.3px}
  .hero-lead b{font-weight:700}
  .hero-claim{margin-top:7px;font-weight:800;text-transform:uppercase;letter-spacing:-.6px}
  .hero-claim .l1{display:block;font-size:40.5px;line-height:44px;color:var(--orange)}
  .hero-claim .l2{display:block;font-size:39.5px;line-height:46px}
  .hero-claim .l3{display:block;font-size:29px;line-height:38px}
  .hero-claim .l4{display:block;font-size:29px;line-height:34px}
  .hero-claim .l4 span{font-size:35.5px;color:var(--orange)}

  .service{position:absolute;white-space:nowrap}
  .service-badge{position:absolute;top:-8px;width:46px;height:46px;border-radius:50%;background:var(--orange);border:2px solid var(--orange);box-shadow:inset 0 0 0 1.5px var(--white)}
  .service-title{font-size:24px;font-weight:600;line-height:30px;letter-spacing:-.3px}
  .service-title span{color:var(--orange)}
  .service-intro{font-size:13.8px;font-weight:500;line-height:19px}
  .bullets{list-style:none}
  .bullets li{position:relative;font-size:13px;line-height:20.3px}
  .bullets li::before{content:"";position:absolute;left:2px;top:6px;width:8px;height:8px;border-radius:50%;background:var(--blue)}
  .cols{position:relative}
  .cols .bullets{position:absolute;top:0}

  .cta{position:absolute;left:31px;top:1058px;color:var(--white);line-height:1;white-space:nowrap}
  .cta-lead{display:block;font-size:26.5px;font-weight:700;letter-spacing:-.3px}
  .cta-main{display:block;font-size:54px;font-weight:800;letter-spacing:-.8px;margin-top:1px}
  .contact-phone{position:absolute;left:73px;top:1148px;font-size:26px;font-weight:700;line-height:32px;color:var(--white)}
  .contact-web{position:absolute;left:320px;top:1154px;font-size:15px;font-weight:500;line-height:20px;color:var(--white)}
</style>
</head>
<body>
<div class="flyer">
  <svg class="shapes" width="849" height="1200" viewBox="0 0 849 1200">
    <polygon points="0,0 314,0 380,144 0,144" fill="var(--black)"/>
    <polygon points="0,144 380,144 455,305 353,479 0,479" fill="var(--blue)"/>
    <polygon points="332,0 610,0 839,499 365,499 470,305" fill="#c9c8c6" role="img" aria-label="Photo of a modern kitchen with dark wood cabinets, white counters and black pendant lamps"/>
    <polygon points="628,0 849,0 849,499" fill="#bcd2d4" role="img" aria-label="Photo of a bright bathroom with glass shower and wall sconces"/>
    <polygon points="436,925 849,925 849,1181 551,1181" fill="#e6ddd3" role="img" aria-label="Photo of a cozy bedroom with a round mirror and soft bedding"/>
    <polygon points="0,1042 480,1042 566,1191 688,1191 688,1200 0,1200" fill="var(--blue)"/>
    <g fill="none" stroke="var(--orange)" stroke-width="2">
      <circle cx="49" cy="1164" r="12"/>
      <path d="M44 1157c-2 2-1 6 3 10s8 5 10 3l-3-3-2 1c-2-1-4-3-5-5l1-2z" fill="var(--orange)" stroke="none"/>
    </g>
    <g fill="none" stroke="var(--orange)" stroke-width="1.8">
      <circle cx="295" cy="1164" r="11"/>
      <ellipse cx="295" cy="1164" rx="5" ry="11"/>
      <line x1="284" y1="1164" x2="306" y2="1164"/>
      <line x1="286" y1="1158" x2="304" y2="1158"/>
      <line x1="286" y1="1170" x2="304" y2="1170"/>
    </g>
  </svg>

  <div class="brand">
    <span class="brand-name">NORTHLINE</span>
    <span class="brand-tag">ROOFING AND EXTERIORS</span>
  </div>

  <div class="hero">
    <p class="hero-lead">Ready for a<br>Beautiful and Funtional<br><b>Kitchen</b> or <b>Bathroom</b>?</p>
    <p class="hero-claim">
      <span class="l1">Work with a</span>
      <span class="l2">Top-Rated Local</span>
      <span class="l3">Remodeling Company</span>
      <span class="l4">In <span>Ankeny, IA</span></span>
    </p>
  </div>

  <section class="service kitchen" style="left:83px;top:531px">
    <span class="service-badge" style="left:-59px"></span>
    <h2 class="service-title">KITCHEN <span>REMODELING</span></h2>
    <p class="service-intro" style="margin-top:6.5px">Whatever your vision is for your new kitchen,<br>our crew can help you bring it to life,You can<br>trust us for:</p>
    <ul class="bullets" style="margin-top:11.5px">
      <li style="padding-left:24px">Open concept design services</li>
      <li style="padding-left:24px">Kitchen cabinet installation services</li>
      <li style="padding-left:24px">Kitchen countertop installation services</li>
      <li style="padding-left:24px">Tile installation services</li>
      <li style="padding-left:24px">Lighting installation services</li>
      <li style="padding-left:24px">Plumbing upgrade services</li>
      <li style="padding-left:24px">Electrical upgrade services</li>
      <li style="padding-left:24px">Drywall services</li>
      <li style="padding-left:24px">Painting services</li>
    </ul>
  </section>

  <section class="service bathroom" style="left:83px;top:835px">
    <span class="service-badge" style="left:-59px"></span>
    <h2 class="service-title">BATHROOM <span>REMODELING</span></h2>
    <p class="service-intro" style="margin-top:8.5px">When you hire us for your bathroom remod-<br>eling project, the possibilities are endless.<br>Our experienced and talented team can:</p>
    <ul class="bullets" style="margin-top:8.5px">
      <li style="padding-left:24px;line-height:20.5px">Install a custom tile shower</li>
      <li style="padding-left:24px;line-height:20.5px">Build a new vanity</li>
      <li style="padding-left:24px;line-height:20.5px">Install flooring and tile</li>
      <li style="padding-left:24px;line-height:20.5px">Replace your plumbing and light fixtures</li>
    </ul>
  </section>

  <section class="service additions" style="left:496px;top:531px">
    <span class="service-badge" style="left:-59px"></span>
    <h2 class="service-title">HOME <span>ATTITIONS</span></h2>
    <p class="service-intro" style="margin-top:5.5px">No matter what kind of space you need, our<br>team will bring your vision to life. You can<br>hire us if you need a:</p>
    <div class="cols" style="margin-top:9px;height:82px">
      <ul class="bullets" style="left:0">
        <li style="padding-left:23px;line-height:20px">Bathroom addition</li>
        <li style="padding-left:23px;line-height:20px">Bedroom addition</li>
        <li style="padding-left:23px;line-height:20px">Garage addition</li>
        <li style="padding-left:23px;line-height:20px">Basement addition</li>
      </ul>
      <ul class="bullets" style="left:165px">
        <li style="padding-left:19px;line-height:20px">Guest room addition</li>
        <li style="padding-left:19px;line-height:20px">Living room addition</li>
        <li style="padding-left:19px;line-height:20px">Sunroom addition</li>
      </ul>
    </div>
  </section>

  <section class="service decks" style="left:496px;top:730px">
    <span class="service-badge" style="left:-59px"></span>
    <h2 class="service-title">DECKS/ <span>PATIOS</span></h2>
    <p class="service-intro" style="margin-top:4.5px">An outdoor space is a great addition to any<br>residential property. When you decide to<br>build a patio or deck, you”ll be able to expri-<br>ence a variety of benefits. Your outdoor area<br>will increase your:</p>
    <div class="cols" style="margin-top:7.5px;height:40px">
      <ul class="bullets" style="left:0">
        <li style="padding-left:23px;line-height:20px">Property value</li>
        <li style="padding-left:23px;line-height:20px">Functional living space</li>
      </ul>
      <ul class="bullets" style="left:125px">
        <li style="padding-left:21px;line-height:20px">Curb appeal</li>
      </ul>
    </div>
  </section>

  <div class="cta">
    <span class="cta-lead">CALL TODAY FOR YOUR</span>
    <span class="cta-main">FREE ESTIMATE</span>
  </div>
  <span class="contact-phone">555-014-2783</span>
  <span class="contact-web">www.northlineiowa.com</span>
</div>
</body>
</html>
```